Hello Creative Minds!
Our business is after a elegant and classy flyer that draws attention!
The business is Velvet Turf - Lawn Revival Services. We provide services that maintain a healthy and vibrant green lawn through the tough Australian seasons. The products we use limits the water needed to keep grass green to a minimum - practically none at all! This not only helps the home owner or home seller but the environment by limiting the use of water that is needed to create a green lawn. The products we use are made from natural ingredients that are and pet friendly.
This fly will be our introductory offer to the market. Below are the required points that need to be on the flyer. Attached is the business logo, before & after pictures and 1 example of the LAYOUT not DESIGN of what the flyer should be laid out like or similar to. Feel free to use different 'Lawn Mower' pictures.
All the best; if you need any questions answered please feel free to message.
REQUIRED POINTS (Please re-phrase were possible);
*Instantly restores the natural green colour of grass – year round
*Lasts for up to 3 months
*Substantially reduces watering needs
*Pet friendly
*Stays green during droughts and water restrictions
*UV fade resistant
*Won’t bleed, run, or stain once absorbed into the grass
*Safe for the environment, pets and people
*Works in extreme heat, cold and frost
*Organic and natural – no harmful chemicals
*Reduces the amount of fertilizer
and water used on lawns
*Kerb appeal is essential for getting your property sold for the highest price possible
SERVICES & PRICING
Lawn maintenance (cut & trim) starting from $60
Lawn rejuvenation starting from $80 (Only $27 a month for 3 months)*
Package deal starting from $120
Introductory offer: 25% off all services. Refer a friend, when they book you receive another 25% off your next service.
LOCATIONS
Nowra to Sydney
CONTACT NUMBER
Will be posted with the winner - please leave an area for this.
SOCIAL MEDIA
Please add Chatterbook and Snapgrid logo's
Updates
Target Market(s)
home owners, home sellers, property developers, real estates and nursing homes and government housing.
Industry/Entity Type
Lawn Care
Look and feel
Each slider illustrates characteristics of the customer's brand and the style your logo design should communicate.

```html
<!DOCTYPE html>
<html lang="en">
<head>
<meta charset="utf-8">
<title>Velvet Turf – Flyer Front and Back</title>
<link rel="stylesheet" href="https://fonts.googleapis.com/css2?family=Poppins:wght@400;500;600;700&family=Playfair+Display:wght@700&display=swap">
<style>
  :root {
    --ink: #333333;
    --ink-soft: #3c3c3c;
    --lime: #9dca3c;
    --lime-ring: #a3d451;
    --meadow: #c2e59c;
    --sky-top: #bfe8e5;
    --mint-bottom: #c9f6cb;
    --paper: #ffffff;
    --grass-dark: #3f8f2a;
    --grass-light: #7cc04a;
    --straw: #b59e72;
    --straw-light: #d8c9a4;
    --yard-soft: #8fa07a;
    --yard-deep: #66834a;
  }
  * { box-sizing: border-box; margin: 0; padding: 0; }
  html, body {
    width: 1200px; height: 867px; overflow: hidden;
    background: var(--paper);
    font-family: "Poppins", sans-serif;
    color: var(--ink);
  }
  .sheet { position: relative; width: 1200px; height: 867px; }
  .side-label {
    position: absolute; top: 11px; width: 551px;
    text-align: center; font-weight: 500; font-size: 16px; color: var(--ink);
  }
  .flyer {
    position: absolute; top: 38px; width: 551px; height: 790px;
    overflow: hidden;
    box-shadow: 0 1px 4px rgba(0,0,0,0.35);
  }
  .flyer--front { left: 38px; }
  .flyer--back { left: 611px; }
  .flyer__art { position: absolute; inset: 0; }
  .flyer > * { position: absolute; }

  .brand-name {
    left: 27px; top: 36px;
    font-weight: 600; font-size: 26px; color: var(--ink-soft);
    letter-spacing: 0.5px;
  }

  .hero-title {
    left: 26px; top: 198px;
    font-weight: 700; font-size: 37px; line-height: 43px; color: var(--ink);
  }
  .hero-offer {
    left: 27px; top: 289px;
    font-weight: 600; font-size: 20px; line-height: 28px; color: var(--ink-soft);
  }

  .section-title { font-weight: 500; font-size: 21px; color: var(--ink); }
  .offer-title { left: 27px; top: 442px; }
  .offer-text {
    left: 26px; top: 484px; width: 230px;
    font-size: 17.5px; line-height: 20.5px; color: var(--ink-soft);
  }
  .location-title { left: 27px; top: 593px; }
  .location-text { left: 26px; top: 637px; font-size: 17.5px; color: var(--ink-soft); }

  .services-title { left: 322px; top: 377px; }
  .service { left: 279px; display: flex; align-items: flex-start; gap: 13px; }
  .service--maintenance { top: 432px; }
  .service--rejuvenation { top: 494px; }
  .service--package { top: 557px; }
  .price-badge {
    width: 30px; height: 30px; border-radius: 3px;
    background: var(--lime); color: var(--paper);
    font-family: "Playfair Display", serif; font-weight: 700; font-size: 11px;
    display: flex; align-items: center; justify-content: center;
    margin-top: 3px;
  }
  .service__name { font-weight: 500; font-size: 21px; line-height: 24px; color: var(--ink); }
  .service__detail { font-size: 14.5px; line-height: 17px; color: var(--ink-soft); }

  .call-line { left: 26px; top: 740px; font-weight: 600; font-size: 22px; color: var(--ink); }

  .socials {
    right: 26px; top: 745px;
    display: flex; flex-direction: column; gap: 2px; align-items: flex-end;
  }
  .social {
    display: flex; align-items: center; gap: 4px;
    font-size: 10px; font-weight: 500; color: var(--ink-soft); line-height: 11px;
  }
  .social__dot { width: 8px; height: 8px; border-radius: 2px; background: var(--lime); }

  .features-title { left: 28px; top: 399px; }
  .feature-list {
    left: 28px; top: 435px; list-style: none;
  }
  .feature {
    display: flex; align-items: center; gap: 15px;
    height: 28px; font-size: 15.5px; color: var(--ink-soft);
  }
  .feature__tick { width: 14px; height: 14px; flex: none; }
</style>
</head>
<body>
<svg width="0" height="0" style="position:absolute" aria-hidden="true">
  <symbol id="tick-icon" viewBox="0 0 24 24">
    <path d="M21 11.1V12a9 9 0 1 1-5.3-8.2" fill="none" stroke="#333" stroke-width="2.4" stroke-linecap="round"/>
    <path d="M21 4.5 12 13.5 9 10.5" fill="none" stroke="#333" stroke-width="2.4" stroke-linecap="round" stroke-linejoin="round"/>
  </symbol>
</svg>

<main class="sheet">
  <div class="side-label" style="left:38px">Front</div>
  <div class="side-label" style="left:611px">Back</div>

  <!-- Front side -->
  <section class="flyer flyer--front">
    <svg class="flyer__art" width="551" height="790" viewBox="0 0 551 790">
      <defs>
        <linearGradient id="front-bg" x1="0" y1="0" x2="0" y2="1">
          <stop offset="0" stop-color="var(--sky-top)"/>
          <stop offset="1" stop-color="var(--mint-bottom)"/>
        </linearGradient>
        <radialGradient id="turf-fill" cx="0.55" cy="0.45" r="0.6">
          <stop offset="0" stop-color="var(--grass-light)"/>
          <stop offset="1" stop-color="var(--grass-dark)"/>
        </radialGradient>
      </defs>
      <rect width="551" height="790" fill="url(#front-bg)"/>
      <circle cx="613" cy="544" r="354" fill="var(--meadow)"/>
      <circle cx="92" cy="272" r="152" fill="var(--lime)"/>
      <g role="img" aria-label="Close-up photo of a lush green lawn">
        <circle cx="422" cy="123" r="232" fill="url(#turf-fill)" stroke="var(--lime-ring)" stroke-width="7"/>
      </g>
    </svg>

    <div class="brand-name">Velvet Turf</div>

    <h1 class="hero-title">Velvet<br>Turf</h1>
    <p class="hero-offer">25% OFF<br>ON ALL SERVICES</p>

    <h2 class="section-title offer-title">Offer</h2>
    <p class="offer-text">Refer a friend, when they book you receive another 25% off your next service.</p>

    <h2 class="section-title location-title">Location</h2>
    <p class="location-text">Nowra to Sydney</p>

    <h2 class="section-title services-title">Our Services</h2>
    <div class="service service--maintenance">
      <span class="price-badge">$60</span>
      <div><div class="service__name">Lawn Maintenance</div><div class="service__detail">Cut &amp; Trim</div></div>
    </div>
    <div class="service service--rejuvenation">
      <span class="price-badge">$80</span>
      <div><div class="service__name">Lawn Rejuvenation</div><div class="service__detail">$27/month - for 3 months</div></div>
    </div>
    <div class="service service--package">
      <span class="price-badge">$120</span>
      <div><div class="service__name">Package Deal</div><div class="service__detail">Starting from $127</div></div>
    </div>

    <p class="call-line">Call Us At 000 987 6543</p>
    <div class="socials">
      <span class="social"><span class="social__dot"></span>Chatterbook</span>
      <span class="social"><span class="social__dot"></span>Snapgrid</span>
    </div>
  </section>

  <!-- Back side -->
  <section class="flyer flyer--back">
    <svg class="flyer__art" width="551" height="790" viewBox="0 0 551 790">
      <defs>
        <linearGradient id="back-bg" x1="0" y1="0" x2="0" y2="1">
          <stop offset="0" stop-color="var(--sky-top)"/>
          <stop offset="1" stop-color="var(--mint-bottom)"/>
        </linearGradient>
        <linearGradient id="yard-fill" x1="0" y1="0" x2="1" y2="1">
          <stop offset="0" stop-color="var(--yard-soft)"/>
          <stop offset="1" stop-color="var(--yard-deep)"/>
        </linearGradient>
        <linearGradient id="straw-fill" x1="0" y1="0" x2="1" y2="1">
          <stop offset="0" stop-color="var(--straw-light)"/>
          <stop offset="1" stop-color="var(--straw)"/>
        </linearGradient>
        <linearGradient id="revived-fill" x1="0" y1="0" x2="1" y2="1">
          <stop offset="0" stop-color="#5f8c3a"/>
          <stop offset="1" stop-color="#3e6b26"/>
        </linearGradient>
        <clipPath id="compare-clip"><circle cx="139" cy="238" r="116"/></clipPath>
        <path id="label-arc" d="M 9 238 A 130 130 0 0 0 269 238"/>
      </defs>
      <rect width="551" height="790" fill="url(#back-bg)"/>
      <g role="img" aria-label="Before and after photos of a backyard lawn beside a paved patio">
        <circle cx="434" cy="121" r="233" fill="url(#yard-fill)" stroke="var(--lime-ring)" stroke-width="7"/>
      </g>
      <g role="img" aria-label="Split close-up of dry straw-coloured grass beside revived green grass" clip-path="url(#compare-clip)">
        <rect x="23" y="122" width="116" height="232" fill="url(#straw-fill)"/>
        <rect x="139" y="122" width="116" height="232" fill="url(#revived-fill)"/>
      </g>
      <text font-family="Poppins, sans-serif" font-weight="600" font-size="17" fill="#333" text-anchor="middle">
        <textPath href="#label-arc" startOffset="42.8%">Before</textPath>
      </text>
      <text font-family="Poppins, sans-serif" font-weight="600" font-size="17" fill="#333" text-anchor="middle">
        <textPath href="#label-arc" startOffset="59%">After</textPath>
      </text>
    </svg>

    <div class="brand-name">Velvet Turf</div>

    <h2 class="section-title features-title">Features</h2>
    <ul class="feature-list">
      <li class="feature"><svg class="feature__tick"><use href="#tick-icon"/></svg>UV fade resistant</li>
      <li class="feature"><svg class="feature__tick"><use href="#tick-icon"/></svg>Pet friendly</li>
      <li class="feature"><svg class="feature__tick"><use href="#tick-icon"/></svg>Stays green during droughts and water restrictions</li>
      <li class="feature"><svg class="feature__tick"><use href="#tick-icon"/></svg>Lasts for up to 3 months</li>
      <li class="feature"><svg class="feature__tick"><use href="#tick-icon"/></svg>Instantly restores the natural green colour of grass</li>
      <li class="feature"><svg class="feature__tick"><use href="#tick-icon"/></svg>Substantially reduces watering needs</li>
      <li class="feature"><svg class="feature__tick"><use href="#tick-icon"/></svg>Won’t bleed, run, or stain once absorbed into the grass</li>
      <li class="feature"><svg class="feature__tick"><use href="#tick-icon"/></svg>Safe for the environment, pets and people</li>
      <li class="feature"><svg class="feature__tick"><use href="#tick-icon"/></svg>Works in extreme heat, cold and frost</li>
      <li class="feature"><svg class="feature__tick"><use href="#tick-icon"/></svg>Organic and natural – no harmful chemicals</li>
    </ul>

    <p class="call-line">Call Us At 000 987 6543</p>
    <div class="socials">
      <span class="social"><span class="social__dot"></span>Chatterbook</span>
      <span class="social"><span class="social__dot"></span>Snapgrid</span>
    </div>
  </section>
</main>
</body>
</html>
```